Kestrada LLC, needs a web page no more than 5 pages (for now)

Kestrada is a general contractor. Our services include general contracting, design-build construction, disaster recovery and environmental remediation. Our main clients are PMX, TQ, State and Local Gov't Agencies, Hospitals and Schools. Kestrada is also a SDVOSB.

```html
<!DOCTYPE html>
<html lang="en">
<head>
<meta charset="utf-8">
<title>Kestrada LLC — General Contracting</title>
<link href="https://fonts.googleapis.com/css2?family=Poppins:wght@400;500;600;700&display=swap" rel="stylesheet">
<style>
:root{
  --black:#000;
  --ink:#111;
  --charcoal:#1b1b1b;
  --gold:#d9ab3f;
  --gold-deep:#b98a24;
  --gold-light:#f2d27a;
  --white:#fff;
  --muted:#d0d0d0;
}
*{box-sizing:border-box;margin:0;padding:0}
html,body{width:1200px;height:3956px;overflow:hidden}
body{font-family:"Poppins",sans-serif;background:var(--black);color:var(--white);position:relative}
section,header,footer{position:absolute;left:0;width:1200px}
.abs{position:absolute}
.brand{font-weight:600;color:var(--gold);letter-spacing:1px;display:flex;align-items:center;gap:8px}
.brand-dot{width:14px;height:14px;border-radius:50%;background:var(--gold)}
.gold-bg{background:linear-gradient(160deg,#f3d57d 0%,#d9ab3f 35%,#c89a2e 55%,#eccb6c 80%,#d8ab44 100%)}
.h2{font-weight:700;font-size:32px;line-height:1.2}
.sub{font-size:13px}
.btn{position:absolute;display:flex;align-items:center;justify-content:center;font-size:13px;font-weight:500;border-radius:4px}

/* nav */
.site-nav{top:0;height:95px;background:var(--black)}
.nav-links{left:307px;top:36px;display:flex;gap:32px;font-size:15px;color:var(--gold)}
.nav-social{left:912px;top:36px;display:flex;gap:26px}
.nav-social span{width:16px;height:16px;border:2px solid var(--gold);border-radius:3px;display:block}

/* hero */
.hero{top:95px;height:520px}
.hero-photo{inset:0;background:linear-gradient(100deg,#2d2f33 0%,#4a4a45 40%,#8a6a2c 65%,#5c5040 100%)}
.hero-shade{inset:0;background:linear-gradient(90deg,rgba(0,0,0,.55),rgba(0,0,0,0) 60%)}
.hero h1{left:110px;top:142px;font-size:46px;font-weight:600;line-height:1.13}
.hero p{left:112px;top:262px;font-size:15px;line-height:1.25;width:420px}
.arrow{left:1152px;top:242px;width:38px;height:38px;border-radius:50%;background:rgba(217,171,63,.8)}

/* projects */
.projects{top:615px;height:699px;color:var(--ink)}
.card-img{width:335px;height:334px;top:170px}
.caption{top:525px;font-size:15px;font-weight:500}
.track{left:112px;top:606px;width:682px;height:4px;background:rgba(0,0,0,.15);border-radius:2px}
.track i{display:block;width:182px;height:4px;background:#222;border-radius:2px}

/* about */
.about{top:1314px;height:487px;background:var(--charcoal)}
.about-text{left:642px;top:181px;width:444px;font-size:13.5px;line-height:1.5}

/* services */
.services{top:1801px;height:545px;background:var(--black)}
.svc{top:169px;width:236px;height:300px}
.svc-img{inset:0}
.svc-band{left:0;right:0;bottom:0;height:57px;background:rgba(200,154,46,.92);text-align:center;padding-top:11px}
.svc-band b{display:block;font-size:15px;font-weight:600}
.svc-band small{font-size:10px}

/* clients */
.clients{top:2346px;height:404px;color:var(--ink)}
.seal{top:174px;width:132px;height:132px;border-radius:50%}
.seal-label{top:323px;width:200px;text-align:center;font-size:16px;font-weight:500;line-height:1.2}

/* why */
.why{top:2750px;height:520px;background:var(--black);text-align:center}
.why-ring{top:178px;width:157px;height:157px;border-radius:50%;border:2px dashed var(--gold);display:flex;align-items:center;justify-content:center}
.why-label{top:350px;width:260px;font-size:17px;font-weight:600;line-height:1.2}

/* contact */
.contact{top:3270px;height:368px;color:var(--white)}
.contact-photo{left:680px;top:-80px;width:470px;height:448px;background:linear-gradient(180deg,rgba(0,0,0,0) 0%,rgba(160,120,40,.55) 40%,rgba(120,95,60,.7) 100%)}

/* footer */
.site-footer{top:3638px;height:318px;background:var(--black)}
.col h4{font-size:15px;font-weight:500;margin-bottom:16px}
.col a{display:block;font-size:13px;color:var(--white);text-decoration:none;margin-bottom:15px}
</style>
</head>
<body>

<header class="site-nav">
  <div class="abs brand" style="left:112px;top:30px;font-size:20px"><span class="brand-dot"></span>KESTRADA</div>
  <nav class="abs nav-links"><span>Home</span><span>About</span><span>Services</span><span>Our Clients</span><span>Projects</span><span>Contact Us</span></nav>
  <div class="abs nav-social"><span></span><span></span><span></span></div>
  <svg class="abs" style="left:1060px;top:40px" width="28" height="16"><path d="M4 4h22M0 11h22" stroke="#d9ab3f" stroke-width="2"/></svg>
</header>

<section class="hero">
  <div class="abs hero-photo" role="img" aria-label="Engineers in hard hats and safety vests reviewing plans on a building site"></div>
  <div class="abs hero-shade"></div>
  <h1 class="abs">Building with Precision.<br>Serving with Kestrada.</h1>
  <p class="abs">General Contracting • Design-Build • Disaster Recovery • Environmental Remediation</p>
  <div class="btn" style="left:113px;top:323px;width:192px;height:50px;background:var(--gold);color:var(--white);font-size:14px">Work With Us</div>
  <div class="abs arrow"><svg width="38" height="38"><path d="M16 12l7 7-7 7" fill="none" stroke="#fff" stroke-width="2"/></svg></div>
</section>

<section class="projects gold-bg">
  <h2 class="abs h2" style="left:112px;top:60px">Recent Projects</h2>
  <p class="abs sub" style="left:112px;top:108px;color:#4a3a18">Lorem Ipsum is simply dummy text of the printing and typesetting industry.</p>
  <div class="btn" style="left:953px;top:92px;width:134px;height:36px;background:var(--ink);color:var(--white)">View More</div>
  <div class="abs card-img" style="left:112px;background:linear-gradient(160deg,#26313a,#4d5a46)" role="img" aria-label="Service members reviewing a laptop in a facility"></div>
  <div class="abs card-img" style="left:464px;background:linear-gradient(180deg,#cfd8e0,#8a6f5a)" role="img" aria-label="Hospital building under construction with cranes"></div>
  <div class="abs card-img" style="left:816px;background:linear-gradient(180deg,#b9c4cf,#6d6a5e)" role="img" aria-label="Waterline pipe being laid by a drilling rig"></div>
  <div class="abs card-img" style="left:1168px;width:32px;background:#e6d7a8" role="img" aria-label="Further project photo"></div>
  <div class="abs caption" style="left:112px">Military / PMX Renovations</div>
  <div class="abs caption" style="left:464px">Hospital Renovations</div>
  <div class="abs caption" style="left:816px">Waterlines Construction</div>
  <div class="abs caption" style="left:1166px;color:#6b5424">12 S</div>
  <div class="abs track"><i></i></div>
</section>

<section class="about">
  <div class="abs" style="left:112px;top:81px;width:487px;height:306px;background:linear-gradient(140deg,#d8d4c8,#8d9aa8)" role="img" aria-label="Team leaning over construction blueprints with hard hats"></div>
  <div class="abs" style="left:396px;top:302px;width:174px;height:122px;background:var(--black);display:flex;align-items:center;justify-content:center"><div class="brand" style="font-size:17px"><span class="brand-dot"></span>KESTRADA</div></div>
  <h2 class="abs h2" style="left:642px;top:103px">About Kestrada</h2>
  <p class="abs about-text">Lorem Ipsum is simply dummy text of the printing and typesetting industry. Lorem Ipsum has been the industry's standard dummy text ever since the 1500s, when an unknown printer took a galley of type and scrambled it to make a type specimen book. Lorem Ipsum is simply dummy text of the printing and typesetting industry. Lorem Ipsum has been the industry's standard dummy specimen book.</p>
  <div class="btn" style="left:642px;top:326px;width:135px;height:36px;background:var(--gold)">Learn More</div>
</section>

<section class="services">
  <h2 class="abs h2" style="left:112px;top:56px">Our Services</h2>
  <p class="abs sub" style="left:112px;top:102px">Lorem Ipsum is simply dummy text of the printing and typesetting industry.</p>
  <div class="btn" style="left:936px;top:77px;width:151px;height:36px;background:var(--gold)">View All Services</div>
  <div class="abs svc" style="left:112px"><div class="abs svc-img" style="background:linear-gradient(170deg,#c7c2b6,#6e5a3c)" role="img" aria-label="Contractors in hard hats on a site"></div><div class="abs svc-band"><b>General Contracting</b><small>Learn More</small></div></div>
  <div class="abs svc" style="left:356px"><div class="abs svc-img" style="background:linear-gradient(170deg,#e9e6df,#9aa4ad)" role="img" aria-label="Architects discussing a design"></div><div class="abs svc-band"><b>Design-Build Construction</b><small>Learn More</small></div></div>
  <div class="abs svc" style="left:603px"><div class="abs svc-img" style="background:linear-gradient(170deg,#9da3a6,#3f4a36)" role="img" aria-label="Worker at a disaster recovery site"></div><div class="abs svc-band"><b>Disaster Recovery</b><small>Learn More</small></div></div>
  <div class="abs svc" style="left:851px"><div class="abs svc-img" style="background:linear-gradient(170deg,#c9d3dc,#566b5d)" role="img" aria-label="Worker at an environmental remediation site"></div><div class="abs svc-band"><b>Environmental Remediation</b><small>Learn More</small></div></div>
</section>

<section class="clients gold-bg">
  <h2 class="abs h2" style="left:112px;top:46px">Our Clients</h2>
  <p class="abs sub" style="left:112px;top:100px;color:#4a3a18">Lorem Ipsum is simply dummy text of the printing and typesetting industry.</p>
  <div class="abs seal" style="left:111px;background:#2c3f73"></div><div class="abs seal-label" style="left:77px">PMX</div>
  <div class="abs seal" style="left:315px;background:#2a2f5a"></div><div class="abs seal-label" style="left:281px">TQ</div>
  <div class="abs seal" style="left:519px;background:#3b6a5a"></div><div class="abs seal-label" style="left:485px">State and Local<br>Gov't Agencies</div>
  <div class="abs seal" style="left:722px;background:#1c1c1c"></div><div class="abs seal-label" style="left:688px">Hospitals</div>
  <div class="abs seal" style="left:925px;background:#213a80"></div><div class="abs seal-label" style="left:891px">Schools</div>
</section>

<section class="why">
  <h2 class="abs h2" style="left:0;width:1200px;top:62px">Why Choose Kestrada</h2>
  <p class="abs sub" style="left:0;width:1200px;top:113px">Lorem Ipsum is simply dummy text of the printing and typesetting industry.</p>
  <div class="abs why-ring" style="left:252px"><svg width="70" height="64" fill="none" stroke="#d9ab3f" stroke-width="2.5"><circle cx="35" cy="24" r="7"/><circle cx="15" cy="30" r="6"/><circle cx="55" cy="30" r="6"/><path d="M22 50c0-9 26-9 26 0M4 54c0-8 18-8 18-2M48 52c0-6 18-6 18 2"/><path d="M35 3l2 4 4 .5-3 3 1 4-4-2-4 2 1-4-3-3 4-.5z"/></svg></div>
  <div class="abs why-label" style="left:200px">Veteran-Owned Expertise<br>(SDVOSB)</div>
  <div class="abs why-ring" style="left:530px"><svg width="60" height="66" fill="none" stroke="#d9ab3f" stroke-width="2.5"><path d="M8 4h34l10 10v48H8z"/><path d="M16 22h26M16 30h26M16 38h16"/><circle cx="44" cy="50" r="9"/><path d="M40 50l3 3 5-6"/></svg></div>
  <div class="abs why-label" style="left:478px">Government Contracting<br>Experience</div>
  <div class="abs why-ring" style="left:810px"><svg width="58" height="64" fill="none" stroke="#d9ab3f" stroke-width="3"><path d="M29 4l22 8v18c0 15-10 26-22 30C17 56 7 45 7 30V12z"/><path d="M19 32l7 7 13-14"/></svg></div>
  <div class="abs why-label" style="left:758px">Precision, Safety, And<br>Compliance</div>
</section>

<section class="contact gold-bg">
  <div class="abs contact-photo" role="img" aria-label="Two engineers in hard hats with rolled plans, one pointing upward, over a city outline"></div>
  <div class="abs" style="left:112px;top:63px;font-size:15px">Contact</div>
  <h2 class="abs" style="left:111px;top:98px;font-size:34px;line-height:1.2;font-weight:500">Ready To Start Your<br><b style="font-weight:700">Next Project With Kestrada?</b></h2>
  <p class="abs" style="left:112px;top:184px;width:470px;font-size:12.5px;line-height:1.25;text-align:justify">Lorem Ipsum is simply dummy text of the printing and typesetting industry. Lorem Ipsum has been the industry's standard dummy text ever since the 1500s, when an unknown printer took a galley of type and scrambled it to make a type specimen book.</p>
  <div class="btn" style="left:112px;top:267px;width:260px;height:40px;background:var(--ink);color:var(--white);font-size:14px;border-radius:5px">CONTACT US TODAY</div>
</section>

<footer class="site-footer">
  <div class="abs brand" style="left:112px;top:120px;font-size:30px"><span class="brand-dot" style="width:22px;height:22px"></span>KESTRADA</div>
  <div class="abs col" style="left:421px;top:57px"><h4>Quick Links</h4><a>About</a><a>Services</a><a>Projects</a><a>Clients</a><a>Contact Us</a></div>
  <div class="abs col" style="left:599px;top:57px"><h4>Services</h4><a>General Contracting</a><a>Design-Build Construction</a><a>Disaster Recovery</a><a>Environmental Remediation</a></div>
  <div class="abs col" style="left:843px;top:57px;width:244px"><h4>Contact Us</h4>
    <a style="display:flex;gap:12px;align-items:center"><svg width="14" height="14"><path d="M3 1l3 3-2 2c1 2 2 3 4 4l2-2 3 3-2 2C6 13 1 8 1 3z" fill="#fff"/></svg>1-800-555-0147</a>
    <a style="display:flex;gap:12px;align-items:center"><svg width="14" height="12"><rect x="1" y="1" width="12" height="10" fill="none" stroke="#fff" stroke-width="1.5"/><path d="M1 1l6 5 6-5" fill="none" stroke="#fff" stroke-width="1.5"/></svg>hello@kestrada-build.com</a>
    <div style="border-top:1px solid #555;margin-top:6px;padding-top:18px;display:flex;gap:28px"><span style="width:16px;height:16px;border:2px solid #fff;border-radius:3px"></span><span style="width:16px;height:16px;border:2px solid #fff;border-radius:3px"></span><span style="width:16px;height:16px;border:2px solid #fff;border-radius:3px"></span></div>
  </div>
  <div class="abs" style="left:0;width:1200px;top:290px;text-align:center;font-size:12px;color:var(--muted)">© 2025. All Rights Reserved.</div>
</footer>

</body>
</html>
```